Calendar Design Project: 2025 with Specific Edits

This is a straightforward project where your creativity can shine!
Simply take the existing 2024 calendar and adapt it for 2025 by incorporating the new photos I've attached.
Please keep the overall concept of the 2024 calendar intact—your focus will be on enhancing it with fresh visuals.

I can't wait to see your amazing designs!
I am looking for a talented graphic designer to create a new 2025 calendar with specific adjustments.
Pictures attached.
Requirements:
Calendar Size: 52cm x 34cm
March Folder:
Adjust the image named "attached - DJI-0025" to make the circular road darker to match the rest of the design.
May Folder:
Modify the circled area in the May image to ensure it looks consistent with the other road (reference file: "attached - After").
November Folder:
Clear out the circled area in the November image (reference file: "attached - After1").
Please let me know if you have any questions or need further clarification.
I added to my breif a design i made last year for same client.
2025, calendar should be vertical and not horizontal. and some of the photos attache are "Before" and "After" please include together inside each month of the calendar.
Thank you!
Feel free to adjust any details as necessary!

Hello talented designers!

I’m excited to share that this is my 14th project on the ArtHive platform, and I’ve been fortunate to have successful collaborations in the past. I'm looking forward to creating a new 2025 calendar with your help, and I believe that with your creativity and skills, we can make this project a success as well!

I hope to establish a long-term relationship with a talented team like yours. As an added incentive, I will be offering a bonus for the winner, and I may select more than one winner, so everyone has a chance to shine!

Let’s make something amazing together!

Best
Update:
cancel or before, only place the After picture

Requirements
Must have
• Project Overview Objective: Create a 2025 calendar using the provided images, maintaining the design concept from the 2024 calendar but enhancing it with new visuals. Format: Vertical layout (52cm x 34cm).

```html
<!DOCTYPE html>
<html lang="en">
<head>
<meta charset="utf-8">
<title>Korvan Construction 2025 Calendar</title>
<link href="https://fonts.googleapis.com/css2?family=Open+Sans:wght@400;600;700&display=swap" rel="stylesheet">
<style>
:root{
  --green:#7ed321;
  --green-text:#5fd43a;
  --green-soft:#d6f8b4;
  --cell:#f0f2f3;
  --ink:#1a1a1a;
  --grey:#6b6b6b;
  --paper:#ffffff;
  --bg:#ffffff;
}
*{margin:0;padding:0;box-sizing:border-box}
html,body{width:1200px;height:848px;overflow:hidden;background:var(--bg);font-family:"Open Sans",Arial,sans-serif;color:var(--ink)}
.sheet{position:absolute;top:132px;width:736px;height:1125px;transform:scale(.5231);transform-origin:0 0;background:var(--paper);overflow:hidden;box-shadow:14px 14px 10px rgba(0,0,0,.35)}
.sheet--march{left:8px}.sheet--april{left:410px}.sheet--may{left:808px}
.sheet-art{position:absolute;left:0;top:0;width:736px;height:600px}
.brand{position:absolute;left:66px;top:58px}
.brand-name{font-size:46px;font-weight:700;letter-spacing:1px;color:var(--ink);line-height:1}
.brand-sub{font-size:16px;letter-spacing:1px;color:var(--ink);margin-top:10px}
.title-label{position:absolute;left:35px;top:605px;font-size:30px;color:var(--green-text);line-height:1}
.title-year{position:absolute;left:33px;top:636px;font-size:66px;font-weight:600;line-height:1}
.month-name{position:absolute;right:212px;top:662px;font-size:42px;color:var(--grey);line-height:1;letter-spacing:1px}
.month-grid{position:absolute;left:35px;top:722px;width:490px;display:grid;grid-template-columns:repeat(7,66px);grid-auto-rows:48px;column-gap:4.6px;row-gap:11px}
.month-grid .day-head{height:38px;background:#fafafa;font-size:9.5px;font-weight:600;display:flex;align-items:center;justify-content:center}
.month-grid .day{background:var(--cell);font-size:27px;padding:12px 0 0 9px;line-height:1.2}
.month-grid>:nth-child(7n+1),.month-grid>:nth-child(7n){background:var(--green-soft)}
.mini{position:absolute;left:538px;width:167px}
.mini--first{top:723px}.mini--second{top:928px}
.mini-label{font-size:11px;color:var(--grey);margin-bottom:4px}
.mini-label span{color:var(--green-text)}
.mini-grid{display:grid;grid-template-columns:repeat(7,22px);column-gap:2.2px;row-gap:4px;grid-auto-rows:16px}
.mini-grid>*{background:var(--cell);font-size:8.5px;padding:3px 0 0 3px}
.mini-grid .mini-head{font-size:3.3px;padding:4px 0 0 1px;height:10px}
.mini-grid>:nth-child(7n+1),.mini-grid>:nth-child(7n){background:var(--green-soft)}
.footer{position:absolute;left:40px;top:1072px;width:670px;display:flex;align-items:center;justify-content:space-between;font-size:9px;color:var(--grey);white-space:nowrap}
.footer span{white-space:nowrap}
.footer-brand{font-size:17px;font-weight:700;color:var(--ink);line-height:1}
.footer b{color:var(--green-text);font-weight:600}
</style>
</head>
<body>

<section class="sheet sheet--march">
  <svg class="sheet-art" viewBox="0 0 736 600">
    <defs>
      <linearGradient id="band" x1="0" x2="1"><stop offset="0" stop-color="#f2fde6"/><stop offset=".6" stop-color="#a8ec4e"/><stop offset="1" stop-color="#7ed321"/></linearGradient>
      <linearGradient id="cityPhoto" x1="0" y1="0" x2="0" y2="1"><stop offset="0" stop-color="#c9ced2"/><stop offset=".35" stop-color="#8a8a84"/><stop offset=".75" stop-color="#5d7a45"/><stop offset="1" stop-color="#8a6a4e"/></linearGradient>
    </defs>
    <path d="M0 0H736V85C600 70 500 90 400 120C250 170 120 180 0 165Z" fill="url(#band)"/>
    <path role="img" aria-label="Aerial photo of a new flyover road crossing a dense town" fill="url(#cityPhoto)" d="M0 165C120 180 250 170 400 120C500 90 600 70 736 80V430C600 470 500 490 350 490C200 490 100 500 0 500Z"/>
    <path d="M0 500C100 500 200 490 350 490C500 490 600 470 736 430V590C620 600 450 565 300 525C160 495 60 505 0 498Z" fill="url(#band)"/>
  </svg>
  <div class="brand"><div class="brand-name">KORVAN</div><div class="brand-sub">CONSTRUCTION LTD</div></div>
  <div class="title-label">CALENDAR</div><div class="title-year">2025</div>
  <div class="month-name">MARCH</div>
  <div class="month-grid">
    <div class="day-head">SUNDAY</div><div class="day-head">MONDAY</div><div class="day-head">TUESDAY</div><div class="day-head">WEDNESDAY</div><div class="day-head">THURSDAY</div><div class="day-head">FRIDAY</div><div class="day-head">SATURDAY</div>
    <div class="day">30</div><div class="day">31</div><div class="day"></div><div class="day"></div><div class="day"></div><div class="day"></div><div class="day">1</div>
    <div class="day">2</div><div class="day">3</div><div class="day">4</div><div class="day">5</div><div class="day">6</div><div class="day">7</div><div class="day">8</div>
    <div class="day">9</div><div class="day">10</div><div class="day">11</div><div class="day">12</div><div class="day">13</div><div class="day">14</div><div class="day">15</div>
    <div class="day">16</div><div class="day">17</div><div class="day">18</div><div class="day">19</div><div class="day">20</div><div class="day">21</div><div class="day">22</div>
    <div class="day">23</div><div class="day">24</div><div class="day">25</div><div class="day">26</div><div class="day">27</div><div class="day">28</div><div class="day">29</div>
  </div>
  <div class="mini mini--first"><div class="mini-label">FEBRUARY | <span>2025</span></div>
    <div class="mini-grid">
      <div class="mini-head">SUNDAY</div><div class="mini-head">MONDAY</div><div class="mini-head">TUESDAY</div><div class="mini-head">WEDNESDAY</div><div class="mini-head">THURSDAY</div><div class="mini-head">FRIDAY</div><div class="mini-head">SATURDAY</div>
      <div></div><div></div><div></div><div></div><div></div><div></div><div>1</div>
      <div>2</div><div>3</div><div>4</div><div>5</div><div>6</div><div>7</div><div>8</div>
      <div>9</div><div>10</div><div>11</div><div>12</div><div>13</div><div>14</div><div>15</div>
      <div>16</div><div>17</div><div>18</div><div>19</div><div>20</div><div>21</div><div>22</div>
      <div>23</div><div>24</div><div>25</div><div>26</div><div>27</div><div>28</div><div></div>
    </div></div>
  <div class="mini mini--second"><div class="mini-label">APRIL | <span>2025</span></div>
    <div class="mini-grid">
      <div class="mini-head">SUNDAY</div><div class="mini-head">MONDAY</div><div class="mini-head">TUESDAY</div><div class="mini-head">WEDNESDAY</div><div class="mini-head">THURSDAY</div><div class="mini-head">FRIDAY</div><div class="mini-head">SATURDAY</div>
      <div></div><div></div><div>1</div><div>2</div><div>3</div><div>4</div><div>5</div>
      <div>6</div><div>7</div><div>8</div><div>9</div><div>10</div><div>11</div><div>12</div>
      <div>13</div><div>14</div><div>15</div><div>16</div><div>17</div><div>18</div><div>19</div>
      <div>20</div><div>21</div><div>22</div><div>23</div><div>24</div><div>25</div><div>26</div>
      <div>27</div><div>28</div><div>29</div><div>30</div><div></div><div></div><div></div>
    </div></div>
  <footer class="footer"><span class="footer-brand">KORVAN</span><span><b>T:</b> +2348012345678</span><span><b>E:</b> info@korvanbuild.com</span><span><b>W:</b> www.korvanbuild.com</span><span><b>A:</b> 14 Harbour Lane, Kestrel Park, Lakeview City</span></footer>
</section>

<section class="sheet sheet--april">
  <svg class="sheet-art" viewBox="0 0 736 600">
    <defs>
      <linearGradient id="band2" x1="0" x2="1"><stop offset="0" stop-color="#f2fde6"/><stop offset=".6" stop-color="#a8ec4e"/><stop offset="1" stop-color="#7ed321"/></linearGradient>
      <linearGradient id="roadPhoto" x1="0" y1="0" x2="0" y2="1"><stop offset="0" stop-color="#e4e6e8"/><stop offset=".3" stop-color="#c6c8c6"/><stop offset=".45" stop-color="#5f7a3e"/><stop offset=".6" stop-color="#77746f"/><stop offset="1" stop-color="#4e4d4b"/></linearGradient>
    </defs>
    <path d="M0 0H736V85C600 70 500 90 400 120C250 170 120 180 0 165Z" fill="url(#band2)"/>
    <path role="img" aria-label="Photo of a road roller paving a new highway" fill="url(#roadPhoto)" d="M0 165C120 180 250 170 400 120C500 90 600 70 736 80V430C600 470 500 490 350 490C200 490 100 500 0 500Z"/>
    <path d="M0 500C100 500 200 490 350 490C500 490 600 470 736 430V590C620 600 450 565 300 525C160 495 60 505 0 498Z" fill="url(#band2)"/>
  </svg>
  <div class="brand"><div class="brand-name">KORVAN</div><div class="brand-sub">CONSTRUCTION LTD</div></div>
  <div class="title-label">CALENDAR</div><div class="title-year">2025</div>
  <div class="month-name">APRIL</div>
  <div class="month-grid">
    <div class="day-head">SUNDAY</div><div class="day-head">MONDAY</div><div class="day-head">TUESDAY</div><div class="day-head">WEDNESDAY</div><div class="day-head">THURSDAY</div><div class="day-head">FRIDAY</div><div class="day-head">SATURDAY</div>
    <div class="day"></div><div class="day"></div><div class="day">1</div><div class="day">2</div><div class="day">3</div><div class="day">4</div><div class="day">5</div>
    <div class="day">6</div><div class="day">7</div><div class="day">8</div><div class="day">9</div><div class="day">10</div><div class="day">11</div><div class="day">12</div>
    <div class="day">13</div><div class="day">14</div><div class="day">15</div><div class="day">16</div><div class="day">17</div><div class="day">18</div><div class="day">19</div>
    <div class="day">20</div><div class="day">21</div><div class="day">22</div><div class="day">23</div><div class="day">24</div><div class="day">25</div><div class="day">26</div>
    <div class="day">27</div><div class="day">28</div><div class="day">29</div><div class="day">30</div><div class="day"></div><div class="day"></div><div class="day"></div>
  </div>
  <div class="mini mini--first"><div class="mini-label">MARCH | <span>2025</span></div>
    <div class="mini-grid">
      <div class="mini-head">SUNDAY</div><div class="mini-head">MONDAY</div><div class="mini-head">TUESDAY</div><div class="mini-head">WEDNESDAY</div><div class="mini-head">THURSDAY</div><div class="mini-head">FRIDAY</div><div class="mini-head">SATURDAY</div>
      <div>30</div><div>31</div><div></div><div></div><div></div><div></div><div>1</div>
      <div>2</div><div>3</div><div>4</div><div>5</div><div>6</div><div>7</div><div>8</div>
      <div>9</div><div>10</div><div>11</div><div>12</div><div>13</div><div>14</div><div>15</div>
      <div>16</div><div>17</div><div>18</div><div>19</div><div>20</div><div>21</div><div>22</div>
      <div>23</div><div>24</div><div>25</div><div>26</div><div>27</div><div>28</div><div>29</div>
    </div></div>
  <div class="mini mini--second"><div class="mini-label">MAY | <span>2025</span></div>
    <div class="mini-grid">
      <div class="mini-head">SUNDAY</div><div class="mini-head">MONDAY</div><div class="mini-head">TUESDAY</div><div class="mini-head">WEDNESDAY</div><div class="mini-head">THURSDAY</div><div class="mini-head">FRIDAY</div><div class="mini-head">SATURDAY</div>
      <div></div><div></div><div></div><div></div><div>1</div><div>2</div><div>3</div>
      <div>4</div><div>5</div><div>6</div><div>7</div><div>8</div><div>9</div><div>10</div>
      <div>11</div><div>12</div><div>13</div><div>14</div><div>15</div><div>16</div><div>17</div>
      <div>18</div><div>19</div><div>20</div><div>21</div><div>22</div><div>23</div><div>24</div>
      <div>25</div><div>26</div><div>27</div><div>28</div><div>29</div><div>30</div><div>31</div>
    </div></div>
  <footer class="footer"><span class="footer-brand">KORVAN</span><span><b>T:</b> +2348012345678</span><span><b>E:</b> info@korvanbuild.com</span><span><b>W:</b> www.korvanbuild.com</span><span><b>A:</b> 14 Harbour Lane, Kestrel Park, Lakeview City</span></footer>
</section>

<section class="sheet sheet--may">
  <svg class="sheet-art" viewBox="0 0 736 600">
    <defs>
      <linearGradient id="band3" x1="0" x2="1"><stop offset="0" stop-color="#f2fde6"/><stop offset=".6" stop-color="#a8ec4e"/><stop offset="1" stop-color="#7ed321"/></linearGradient>
      <linearGradient id="fieldPhoto" x1="0" y1="0" x2="1" y2="1"><stop offset="0" stop-color="#6f8a5a"/><stop offset=".4" stop-color="#3f8a2e"/><stop offset=".7" stop-color="#4a9a34"/><stop offset="1" stop-color="#9a6a4e"/></linearGradient>
    </defs>
    <path d="M0 0H736V85C600 70 500 90 400 120C250 170 120 180 0 165Z" fill="url(#band3)"/>
    <path role="img" aria-label="Aerial photo of a new road through green farmland and houses" fill="url(#fieldPhoto)" d="M0 165C120 180 250 170 400 120C500 90 600 70 736 80V430C600 470 500 490 350 490C200 490 100 500 0 500Z"/>
    <path d="M0 500C100 500 200 490 350 490C500 490 600 470 736 430V590C620 600 450 565 300 525C160 495 60 505 0 498Z" fill="url(#band3)"/>
  </svg>
  <div class="brand"><div class="brand-name">KORVAN</div><div class="brand-sub">CONSTRUCTION LTD</div></div>
  <div class="title-label">CALENDAR</div><div class="title-year">2025</div>
  <div class="month-name">MAY</div>
  <div class="month-grid">
    <div class="day-head">SUNDAY</div><div class="day-head">MONDAY</div><div class="day-head">TUESDAY</div><div class="day-head">WEDNESDAY</div><div class="day-head">THURSDAY</div><div class="day-head">FRIDAY</div><div class="day-head">SATURDAY</div>
    <div class="day"></div><div class="day"></div><div class="day"></div><div class="day"></div><div class="day">1</div><div class="day">2</div><div class="day">3</div>
    <div class="day">4</div><div class="day">5</div><div class="day">6</div><div class="day">7</div><div class="day">8</div><div class="day">9</div><div class="day">10</div>
    <div class="day">11</div><div class="day">12</div><div class="day">13</div><div class="day">14</div><div class="day">15</div><div class="day">16</div><div class="day">17</div>
    <div class="day">18</div><div class="day">19</div><div class="day">20</div><div class="day">21</div><div class="day">22</div><div class="day">23</div><div class="day">24</div>
    <div class="day">25</div><div class="day">26</div><div class="day">27</div><div class="day">28</div><div class="day">29</div><div class="day">30</div><div class="day">31</div>
  </div>
  <div class="mini mini--first"><div class="mini-label">APRIL | <span>2025</span></div>
    <div class="mini-grid">
      <div class="mini-head">SUNDAY</div><div class="mini-head">MONDAY</div><div class="mini-head">TUESDAY</div><div class="mini-head">WEDNESDAY</div><div class="mini-head">THURSDAY</div><div class="mini-head">FRIDAY</div><div class="mini-head">SATURDAY</div>
      <div></div><div></div><div>1</div><div>2</div><div>3</div><div>4</div><div>5</div>
      <div>6</div><div>7</div><div>8</div><div>9</div><div>10</div><div>11</div><div>12</div>
      <div>13</div><div>14</div><div>15</div><div>16</div><div>17</div><div>18</div><div>19</div>
      <div>20</div><div>21</div><div>22</div><div>23</div><div>24</div><div>25</div><div>26</div>
      <div>27</div><div>28</div><div>29</div><div>30</div><div></div><div></div><div></div>
    </div></div>
  <div class="mini mini--second"><div class="mini-label">JUNE | <span>2025</span></div>
    <div class="mini-grid">
      <div class="mini-head">SUNDAY</div><div class="mini-head">MONDAY</div><div class="mini-head">TUESDAY</div><div class="mini-head">WEDNESDAY</div><div class="mini-head">THURSDAY</div><div class="mini-head">FRIDAY</div><div class="mini-head">SATURDAY</div>
      <div>29</div><div>30</div><div></div><div></div><div></div><div></div><div></div>
      <div>1</div><div>2</div><div>3</div><div>4</div><div>5</div><div>6</div><div>7</div>
      <div>8</div><div>9</div><div>10</div><div>11</div><div>12</div><div>13</div><div>14</div>
      <div>15</div><div>16</div><div>17</div><div>18</div><div>19</div><div>20</div><div>21</div>
      <div>22</div><div>23</div><div>24</div><div>25</div><div>26</div><div>27</div><div>28</div>
    </div></div>
  <footer class="footer"><span class="footer-brand">KORVAN</span><span><b>T:</b> +2348012345678</span><span><b>E:</b> info@korvanbuild.com</span><span><b>W:</b> www.korvanbuild.com</span><span><b>A:</b> 14 Harbour Lane, Kestrel Park, Lakeview City</span></footer>
</section>

</body>
</html>
```